Business Card Design

We need a design for business cards for our company. We have a logo. We teach EMT's and we are based out of Virginia. The information that will need to add would be, name, title, phone number, email, address. On the back of the business card would be "We help you, help others"

Target Market(s)

People that want to become EMT's

Colors

Designer to choose colors to be used in the design.

Requirements
Must have
• company logo

```html
<!DOCTYPE html>
<html lang="en">
<head>
<meta charset="utf-8">
<title>Ridgeline Medic Academy – Business Card</title>
<link rel="stylesheet" href="https://fonts.googleapis.com/css2?family=Oswald:wght@500&family=Work+Sans:wght@400;500&display=swap">
<style>
  :root {
    --backdrop: #141414;
    --card-edge: #2a2a2a;
    --foil: #cfcfcf;
    --foil-soft: #a9a9a9;
  }
  * { margin: 0; padding: 0; box-sizing: border-box; }
  html, body {
    width: 1200px;
    height: 900px;
    overflow: hidden;
    background: var(--backdrop);
  }
  .canvas {
    width: 1200px;
    height: 900px;
    display: flex;
    flex-direction: column;
    align-items: center;
    justify-content: center;
    gap: 40px;
  }
  .card {
    position: relative;
    width: 630px;
    height: 360px;
    background: linear-gradient(135deg, #1b1b1b 0%, #222 60%, #262626 100%);
    border: 1px solid var(--card-edge);
    box-shadow: 0 14px 30px rgba(0, 0, 0, 0.5);
    color: var(--foil);
    font-family: "Work Sans", sans-serif;
  }
  .card-front {
    display: flex;
    flex-direction: column;
    align-items: center;
    justify-content: center;
    gap: 26px;
  }
  .brand {
    display: flex;
    align-items: center;
    gap: 14px;
  }
  .brand-dot {
    width: 24px;
    height: 24px;
    border-radius: 50%;
    background: var(--foil);
  }
  .brand-name {
    font-family: "Work Sans", sans-serif;
    font-weight: 500;
    font-size: 31px;
    letter-spacing: 1px;
    color: var(--foil);
    text-transform: uppercase;
  }
  .tagline {
    font-size: 15px;
    letter-spacing: 3px;
    text-transform: uppercase;
    color: var(--foil-soft);
  }
  .identity {
    position: absolute;
    right: 360px;
    top: 128px;
    text-align: right;
  }
  .person-name {
    font-family: "Oswald", sans-serif;
    font-weight: 500;
    font-size: 30px;
    letter-spacing: 1.5px;
    text-transform: uppercase;
    color: var(--foil);
    line-height: 1.1;
  }
  .person-title {
    font-size: 15px;
    color: var(--foil-soft);
    letter-spacing: 0.5px;
    margin-top: 4px;
  }
  .divider {
    position: absolute;
    left: 292px;
    top: 122px;
    width: 1px;
    height: 82px;
    background: var(--foil-soft);
  }
  .contact-list {
    position: absolute;
    left: 316px;
    top: 124px;
    list-style: none;
  }
  .contact-item {
    display: flex;
    align-items: center;
    gap: 10px;
    font-size: 17px;
    line-height: 27px;
    color: var(--foil);
  }
  .contact-icon {
    width: 13px;
    height: 13px;
    flex: none;
  }
  .address {
    position: absolute;
    left: 60px;
    bottom: 46px;
    font-size: 16px;
    letter-spacing: 0.4px;
    color: var(--foil-soft);
  }
</style>
</head>
<body>
<main class="canvas">
  <section class="card card-front" aria-label="Card front">
    <div class="brand">
      <span class="brand-dot"></span>
      <span class="brand-name">Ridgeline Medic Academy</span>
    </div>
    <p class="tagline">We help you, help others</p>
  </section>

  <section class="card card-back" aria-label="Card back">
    <div class="identity">
      <p class="person-name">Daniel Hartley</p>
      <p class="person-title">Director</p>
    </div>
    <span class="divider"></span>
    <ul class="contact-list">
      <li class="contact-item">
        <svg class="contact-icon" viewBox="0 0 16 16" aria-hidden="true">
          <path d="M3 1.5 L6 1.5 L7 5 L5.3 6.3 C6.2 8.2 7.8 9.8 9.7 10.7 L11 9 L14.5 10 L14.5 13 C14.5 14 13.7 14.5 13 14.5 C6.9 14.2 1.8 9.1 1.5 3 C1.5 2.3 2 1.5 3 1.5 Z" fill="var(--foil)"/>
        </svg>
        555-214-7730
      </li>
      <li class="contact-item">
        <svg class="contact-icon" viewBox="0 0 16 16" aria-hidden="true">
          <rect x="1.5" y="3.5" width="13" height="9" fill="none" stroke="var(--foil)" stroke-width="1.4"/>
          <path d="M1.5 3.5 L8 9 L14.5 3.5" fill="none" stroke="var(--foil)" stroke-width="1.4"/>
        </svg>
        hello@ridgelinemedic.com
      </li>
      <li class="contact-item">
        <svg class="contact-icon" viewBox="0 0 16 16" aria-hidden="true">
          <circle cx="8" cy="8" r="6.5" fill="none" stroke="var(--foil)" stroke-width="1.3"/>
          <ellipse cx="8" cy="8" rx="2.8" ry="6.5" fill="none" stroke="var(--foil)" stroke-width="1.1"/>
          <path d="M1.5 8 H14.5 M2.6 4.5 H13.4 M2.6 11.5 H13.4" stroke="var(--foil)" stroke-width="1"/>
        </svg>
        www.ridgelinemedic.com
      </li>
    </ul>
    <p class="address">48 Harbor Lane, Lakemont, VA 24000</p>
  </section>
</main>
</body>
</html>
```